Velmora Sports Foundation website

Velmora sports foundation is a charity organisation that assists young athletes and clubs with the financial assistance they need to progress in their sporting career.

The organisation also establishes mentoring programs to community clubs and individuals.
We envision a home page with a horizontal navigation
Contact Us
Donate: A link to a secure payment system
Meet the team: A list of names and images of the board
Lastly the link to donate should be featured prominently and several times along with cues that lead people to find out more
We prefer limited scrolling and would like to see a clean yet modern design

I am unsure if it needs to be coded or not

Target Market(s)

Potential donors, applications for funds, potential affiliates

Industry/Entity Type

Charity

Coding

Coded - Design and coding required

Number of Pages Required

5+ page

Font styles to use
Sans Serif

Colors
3176b5
ec1f27
34a7d7

Requirements
Must have
• emotionally engaging and informative
• motion enabled pictures
• links to donate
• Music
• Enable video uploads
• Large horizontal pictures of young sports players prominently soccer at this stage
• Social media presence
Nice to have
• Live chat
Should not have
• Images that depict poverty

```html
<!DOCTYPE html>
<html lang="en">
<head>
<meta charset="utf-8">
<title>Velmora Sports Foundation</title>
<link href="https://fonts.googleapis.com/css2?family=Montserrat:wght@400;500;600;700&display=swap" rel="stylesheet">
<style>
:root{
  --red:#e3232b;
  --blue:#3176b5;
  --sky:#34a7d7;
  --ink:#2a2a2a;
  --muted:#8a8a8a;
  --page:#f4f4f4;
  --line:#e2e2e2;
  --footer:#333333;
  --footer-text:#c9c9c9;
  --white:#ffffff;
}
*{box-sizing:border-box;margin:0;padding:0}
html,body{width:669px;height:1200px;overflow:hidden}
body{font-family:"Montserrat",Arial,sans-serif;background:var(--page);color:var(--ink);position:relative}
.abs{position:absolute}
.hero-bg{left:0;top:0;width:669px;height:282px;background:linear-gradient(180deg,#3a3a3a 0%,#5a5a5a 55%,#4a4a4a 100%)}
.btn{display:inline-block;background:var(--red);color:var(--white);font-weight:500;text-transform:uppercase;letter-spacing:.5px;text-align:center}
.btn-top{left:502px;top:18px;width:93px;height:23px;line-height:23px;font-size:9px}
.nav a{position:absolute;top:57px;color:var(--white);font-size:8px;font-weight:500;text-decoration:none;letter-spacing:.3px}
.logo{left:278px;top:4px;width:112px;height:112px;border-radius:50%;background:var(--white);box-shadow:0 2px 6px rgba(0,0,0,.25);display:flex;align-items:center;justify-content:center;text-align:center;z-index:3}
.logo span{color:var(--blue);font-weight:700;font-size:10px;line-height:1.25;text-transform:uppercase}
.welcome-card{left:74px;top:79px;width:521px;height:329px;background:var(--white);box-shadow:0 1px 3px rgba(0,0,0,.15)}
.slide{left:79px;top:86px;width:511px;height:236px;background:linear-gradient(180deg,#6e8f3e 0%,#86a84c 60%,#789a40 100%)}
.dots{left:314px;top:298px;display:flex;gap:3px}
.dots i{width:8px;height:8px;border-radius:50%;background:var(--white);border:1px solid var(--white)}
.dots i.off{background:transparent}
.welcome-title{left:74px;top:338px;width:521px;text-align:center;font-size:13.5px;font-weight:600;letter-spacing:.3px}
.welcome-title em{font-style:normal;color:var(--red)}
.welcome-text{left:100px;top:360px;width:469px;text-align:center;font-size:8px;line-height:14px;color:var(--muted)}
.section-title{width:669px;left:0;text-align:center;font-size:13px;font-weight:600;letter-spacing:.5px}
.section-title em{font-style:normal;color:var(--red)}
.rule{left:74px;top:456px;width:521px;height:1px;background:var(--line)}
.service{top:474px;width:121px;height:188px;background:var(--white);border:1px solid #ececec;text-align:center}
.service .photo{margin:8px auto 0;width:105px;height:78px}
.service h3{margin-top:12px;font-size:7.5px;font-weight:500;letter-spacing:.3px}
.service p{margin:10px 9px 0;font-size:6px;line-height:10.5px;color:var(--muted)}
.service .btn{margin-top:9px;width:62px;height:16px;line-height:16px;font-size:6.3px}
.video-band{left:0;top:690px;width:669px;height:208px;background:linear-gradient(180deg,#4a4a4a 0%,#5c5c5c 50%,#474747 100%)}
.video-title{left:0;top:730px;width:669px;text-align:center;color:var(--white);font-size:24px;font-weight:400;line-height:28px;letter-spacing:.5px}
.play{left:306px;top:791px}
.sponsor{top:959px;width:100px;height:39px;border:1px solid #dcdcdc;background:var(--white);transform:skewX(-8deg);display:flex;align-items:center;justify-content:center}
.sponsor span{transform:skewX(8deg);color:#9a9a9a;font-size:10px;font-weight:600;letter-spacing:.5px}
.arrow{top:970px}
footer{left:0;top:1028px;width:669px;height:172px;background:var(--footer);color:var(--footer-text)}
.f-h{position:absolute;top:22px;font-size:9px;color:var(--white);letter-spacing:.4px}
.f-div{position:absolute;top:22px;width:1px;height:96px;background:#4a4a4a}
.f-text{position:absolute;left:74px;top:44px;width:110px;font-size:6px;line-height:9px}
.f-btn{left:74px;top:94px;width:71px;height:20px;line-height:20px;font-size:7px}
.f-links{position:absolute;left:231px;top:42px;list-style:none;font-size:7px;line-height:15.6px}
.chat{position:absolute;left:328px;top:42px;width:119px;height:45px;background:var(--white);border-radius:3px;overflow:hidden}
.chat b{position:absolute;left:10px;top:7px;font-weight:400;font-size:9.5px;color:#444}
.chat small{position:absolute;left:10px;top:20px;font-size:7.5px;color:#444}
.chat .go{position:absolute;left:12px;top:33px;width:56px;height:9px;border-radius:5px;background:#f08c1e;color:var(--white);font-size:6px;line-height:9px;text-align:center}
.chat .agent{position:absolute;right:0;top:0;width:42px;height:45px;background:linear-gradient(180deg,#d9d2cb,#b8b0a8)}
.f-note{position:absolute;left:502px;top:46px;font-size:7px}
.socials{position:absolute;left:502px;top:64px;display:flex;gap:2px}
.socials i{width:20px;height:20px;border-radius:50%;border:2px solid var(--white)}
.f-bottom{position:absolute;left:72px;top:134px;width:522px;height:1px;background:#555}
.copyright{position:absolute;left:72px;top:146px;font-size:6.3px}
</style>
</head>
<body>
<div class="abs hero-bg" role="img" aria-label="Dimmed stadium with floodlights"></div>
<a class="abs btn btn-top">Donate Now !</a>
<nav class="nav">
  <a style="left:90px">HOME</a>
  <a style="left:144px">PROGRAM ⌄</a>
  <a style="left:222px">DONATE</a>
  <a style="left:431px">MEET THE TEAM</a>
  <a style="left:525px">CONTACT US</a>
</nav>
<div class="abs logo"><span>Velmora Sports<br>Foundation</span></div>

<section class="abs welcome-card"></section>
<div class="abs slide" role="img" aria-label="Young soccer player running on a grass pitch"></div>
<div class="abs dots"><i class="off"></i><i></i><i></i><i></i></div>
<h1 class="abs welcome-title">WELCOME TO <em>VELMORA SPORTS FOUNDATION</em></h1>
<p class="abs welcome-text">Sed ut perspiciatis unde omnis iste natus error sit voluptatem accusantium doloremque laudantium, totam rem aperiam, eaque ipsa quae ab illo inventore veritatis et quasi architecto beatae vitae dicta sunt explicabo</p>

<h2 class="abs section-title" style="top:426px">OUR SERVICES</h2>
<div class="abs rule"></div>

<article class="abs service" style="left:74px">
  <div class="photo" role="img" aria-label="Youth soccer match on a green field" style="background:linear-gradient(180deg,#8fa28a,#6c9a3c)"></div>
  <h3>OCCAECAT CUPIDATAT</h3>
  <p>Eaque ipsa quae ab illo inventore veritatis et quasi architecto beatae vitae dicta.</p>
  <a class="btn">Donate Now</a>
</article>
<article class="abs service" style="left:208px">
  <div class="photo" role="img" aria-label="Two young players in blue kits holding balls" style="background:linear-gradient(180deg,#5e9bd6,#8fb5d8 60%,#7d9a55)"></div>
  <h3>MAGNAM ALIQUAM</h3>
  <p>Eaque ipsa quae ab illo inventore veritatis et quasi architecto beatae vitae dicta.</p>
  <a class="btn">Donate Now</a>
</article>
<article class="abs service" style="left:342px">
  <div class="photo" role="img" aria-label="Youth team huddled together with a coach" style="background:linear-gradient(180deg,#d8d4cc,#b8a56a 60%,#8a8a7a)"></div>
  <h3>RATIONE VOLUPTATEM</h3>
  <p>Eaque ipsa quae ab illo inventore veritatis et quasi architecto beatae vitae dicta.</p>
  <a class="btn">Donate Now</a>
</article>
<article class="abs service" style="left:474px">
  <div class="photo" role="img" aria-label="Player striking a ball near the goal" style="background:linear-gradient(180deg,#5f8f3a,#7aa84a)"></div>
  <h3>MINIMA VENIAM</h3>
  <p>Eaque ipsa quae ab illo inventore veritatis et quasi architecto beatae vitae dicta.</p>
  <a class="btn">Donate Now</a>
</article>

<section class="abs video-band" role="img" aria-label="Player standing in a floodlit stadium"></section>
<h2 class="abs video-title">Sports Foundation<br>Watch the Video Now!</h2>
<svg class="abs play" width="56" height="56" viewBox="0 0 56 56" aria-label="Play video">
  <circle cx="28" cy="28" r="25.5" fill="none" stroke="#fff" stroke-width="4"/>
  <path d="M22 16 L40 28 L22 40 Z" fill="#fff"/>
</svg>

<h2 class="abs section-title" style="top:923px">OUR <em>SPONSORS</em></h2>
<svg class="abs arrow" style="left:51px" width="10" height="16" viewBox="0 0 10 16"><path d="M8 2 L2 8 L8 14" fill="none" stroke="#c4c4c4" stroke-width="2.5"/></svg>
<div class="abs sponsor" style="left:78px"><span>STRIDEWELL</span></div>
<div class="abs sponsor" style="left:181px"><span>FIELDMARK</span></div>
<div class="abs sponsor" style="left:285px"><span>KICKLINE</span></div>
<div class="abs sponsor" style="left:388px"><span>NORVANE</span></div>
<div class="abs sponsor" style="left:492px"><span>PELLOW</span></div>
<svg class="abs arrow" style="left:609px" width="10" height="16" viewBox="0 0 10 16"><path d="M2 2 L8 8 L2 14" fill="none" stroke="#c4c4c4" stroke-width="2.5"/></svg>

<footer class="abs">
  <h4 class="f-h" style="left:74px">COMPANY</h4>
  <p class="f-text">Velmora sports foundation is a charity organisation that assists young athletes and clubs with the financial assistance they need to progress in their sporting career.</p>
  <a class="abs btn f-btn">Donate Now!</a>
  <div class="f-div" style="left:202px"></div>
  <h4 class="f-h" style="left:231px">LINKS</h4>
  <ul class="f-links"><li>Home</li><li>Program</li><li>Donate</li><li>Meet the Team</li><li>Contact Us</li></ul>
  <div class="f-div" style="left:302px"></div>
  <h4 class="f-h" style="left:328px">LIVE CHAT</h4>
  <div class="chat">
    <b>Need Help?</b><small>Have a Question?</small>
    <span class="go">Chat Now ›</span>
    <div class="agent" role="img" aria-label="Support agent with headset"></div>
  </div>
  <div class="f-div" style="left:477px"></div>
  <h4 class="f-h" style="left:502px">FOLLOW US</h4>
  <p class="f-note">Please connect with us on</p>
  <div class="socials">
    <i style="background:var(--sky)"></i><i style="background:var(--blue)"></i><i style="background:#2a6fa8"></i><i style="background:var(--red)"></i>
  </div>
  <div class="f-bottom"></div>
  <p class="copyright">© 2016 Company Name &nbsp;All right reserved &nbsp;Term of Use</p>
</footer>
</body>
</html>
```